Business Card Design

New business card design

Target Market(s)

Residential & Commercial Property Managers

Industry/Entity Type

Plumbing Services

Contact Information for Business Card

Name - Rowan Keddle, title - Director, Phone Number - 0431 286 517, email - rowan@tbk-plumbing.com.au, Company ABN - 73 215 904 386,

Font styles to use
Sans Serif

Colors
0054AA
0677BA
7BADD7
CADEEF
E8F1F8

```html
<!DOCTYPE html>
<html lang="en">
<head>
<meta charset="utf-8">
<title>TBK Plumbing Services – Business Card</title>
<link rel="stylesheet" href="https://fonts.googleapis.com/css2?family=Roboto:wght@300;400;700&display=swap">
<style>
  :root {
    --stage: #2b2b2c;
    --card-white: #f6f6f6;
    --card-black: #111112;
    --ink: #141414;
    --ink-soft: #6d6d6d;
    --accent: #0677ba;
    --accent-bright: #1aa3e0;
    --band: #161617;
    --band-text: #e9e9e9;
  }
  * { box-sizing: border-box; margin: 0; padding: 0; }
  html, body {
    width: 1200px; height: 852px; overflow: hidden;
    background: var(--stage);
    font-family: "Roboto", Arial, sans-serif;
  }
  .stage { position: relative; width: 1200px; height: 852px; }

  .card {
    position: absolute; top: 281px;
    width: 508px; height: 290px;
    border-radius: 20px; overflow: hidden;
  }
  .card--back { left: 66px; background: var(--card-black); }
  .card--front { left: 626px; background: var(--card-white); color: var(--ink); }

  .drop-pattern {
    position: absolute; inset: 0;
    background: linear-gradient(160deg, #6a6a6c 0%, #3a3a3c 35%, #151516 65%, #0a0a0a 100%);
  }

  .brand { position: absolute; left: 34px; top: 36px; display: flex; align-items: center; gap: 12px; }
  .brand__dot { width: 14px; height: 14px; border-radius: 50%; background: var(--accent-bright); }
  .brand__name { font-size: 27px; font-weight: 300; letter-spacing: 1px; color: var(--ink); }

  .person { position: absolute; left: 34px; top: 176px; }
  .person__name { font-size: 19px; font-weight: 700; }
  .person__title { font-size: 11.5px; font-weight: 300; color: var(--ink-soft); margin-top: 2px; }
  .person__address { font-size: 11.5px; font-weight: 400; line-height: 1.45; margin-top: 16px; }

  .contacts { position: absolute; left: 300px; top: 102px; list-style: none; }
  .contacts li { display: flex; align-items: center; gap: 8px; font-size: 11.5px; font-weight: 300; line-height: 17px; }
  .contacts svg { width: 10px; height: 10px; fill: var(--accent); flex: none; }
  .contacts__label { width: 10px; flex: none; font-size: 7px; font-weight: 700; color: var(--accent); }

  .company-band {
    position: absolute; right: 0; bottom: 34px;
    width: 232px; height: 32px;
    background: var(--band);
    display: flex; align-items: center; justify-content: flex-end;
    padding-right: 16px;
    color: var(--band-text); font-size: 11px; font-weight: 400;
  }
  .company-band__accent { position: absolute; left: -16px; top: 0; width: 28px; height: 32px; }
</style>
</head>
<body>
<main class="stage">

  <section class="card card--back" aria-label="Card back">
    <div class="drop-pattern" role="img" aria-label="Repeating water-drop pattern in glossy black and grey"></div>
  </section>

  <section class="card card--front" aria-label="Card front">
    <div class="brand">
      <span class="brand__dot"></span>
      <span class="brand__name">TBK Plumbing Services</span>
    </div>

    <div class="person">
      <p class="person__name">Rowan Keddle</p>
      <p class="person__title">Director</p>
      <p class="person__address">18 Harbour Rd., Eastfield,<br>Parramatta, NSW 2150</p>
    </div>

    <ul class="contacts">
      <li><svg viewBox="0 0 10 10"><path d="M2 0h2l1 2.5-1.3 1a6 6 0 0 0 2.8 2.8l1-1.3L10 6v2a2 2 0 0 1-2 2A8 8 0 0 1 0 2a2 2 0 0 1 2-2z"/></svg>0431 286 517</li>
      <li><svg viewBox="0 0 10 10"><path d="M0 2h10v6H0z M0 2l5 3.5L10 2" fill="none" stroke="#0677ba" stroke-width="1.2"/></svg>rowan@tbk-plumbing.com.au</li>
      <li><svg viewBox="0 0 10 10"><circle cx="5" cy="5" r="4.4" fill="none" stroke="#0677ba" stroke-width="1"/><path d="M0.6 5h8.8M5 0.6v8.8" stroke="#0677ba" stroke-width="0.8"/></svg>www.tbk-plumbing.com.au</li>
      <li><span class="contacts__label"></span>ABN 73 215 904 386</li>
    </ul>

    <div class="company-band">
      <svg class="company-band__accent" viewBox="0 0 28 32" aria-hidden="true">
        <path d="M10 0h18v32H0z" fill="var(--accent-bright)"/>
        <path d="M18 0h10v32H10z" fill="var(--band)"/>
      </svg>
      TBK Plumbing Services Pty Ltd.
    </div>
  </section>

</main>
</body>
</html>
```